At Home Pet Euthanasia - business cards & brand stationary

We already have a logo and the colors and a website. Need a business card designed that will be able to customized to multiple veterinarians who will be partnering with us. The feel needs to be compassionate, comforting with our tagline 'A Gift of Love at Home'. It will be 2 sides.
On the back our platform/partner vets will be customizing each business card with their own service areas, phone numbers, name and title. On the front, i would like to see experimentation with use of our photos, the logo, tagline and a description 'Peaceful and Compassionate At-Home Pet Euthanasia'

```html
<!DOCTYPE html>
<html lang="en">
<head>
<meta charset="utf-8">
<title>Restwell Business Card</title>
<link href="https://fonts.googleapis.com/css2?family=Arimo:wght@400;700&display=swap" rel="stylesheet">
<style>
  :root {
    --backdrop: #262626;
    --card-black: #0e0e0e;
    --brand-blue: #7d9dcb;
    --text-white: #f2f2f2;
    --rule-grey: #555555;
    --photo-light: #9a9a9a;
    --photo-dark: #3e3e3e;
  }
  * { box-sizing: border-box; margin: 0; padding: 0; }
  html, body {
    width: 1200px; height: 900px; overflow: hidden;
    background: var(--backdrop);
    font-family: "Arimo", Arial, sans-serif;
  }
  .card {
    position: absolute; left: 320px;
    width: 560px; height: 320px;
    border-radius: 22px; overflow: hidden;
    box-shadow: 0 14px 30px rgba(0,0,0,.55);
  }
  .card--details { top: 90px; background: var(--card-black); }
  .card--photo { top: 490px; }

  .brand {
    position: absolute; display: flex; align-items: center; gap: 10px;
    color: var(--brand-blue); font-weight: 700; white-space: nowrap;
  }
  .brand__mark { width: 30px; height: 30px; background: var(--brand-blue); border-radius: 4px; flex: none; }
  .card--details .brand { left: 40px; top: 150px; font-size: 38px; }

  .divider {
    position: absolute; left: 282px; top: 40px; width: 1px; height: 190px;
    background: var(--rule-grey);
  }
  .contact { position: absolute; left: 306px; top: 42px; color: var(--text-white); }
  .contact__name { color: var(--brand-blue); font-weight: 700; font-size: 19px; letter-spacing: .5px; }
  .contact__title { font-size: 15px; margin-bottom: 14px; }
  .contact__row { display: flex; align-items: center; gap: 9px; font-size: 15px; line-height: 22px; }
  .contact__row svg { width: 15px; height: 15px; flex: none; }
  .contact__address { font-size: 15px; line-height: 19px; margin-top: 12px; padding-left: 24px; }
  .accent { color: var(--brand-blue); }

  .tagline-band {
    position: absolute; left: 0; bottom: 34px; width: 100%; height: 38px;
    background: var(--brand-blue); display: flex; align-items: center; padding-left: 36px;
    font-weight: 700; font-size: 14px; letter-spacing: .4px; color: var(--card-black);
    white-space: nowrap;
  }

  .photo-fill {
    position: absolute; inset: 0;
    background: radial-gradient(ellipse at 55% 55%, var(--photo-light), var(--photo-dark) 85%);
  }
  .card--photo .brand { right: 34px; top: 30px; font-size: 40px; }
  .brand-line {
    position: absolute; right: 36px; top: 82px;
    color: var(--brand-blue); font-size: 12px; font-weight: 700; letter-spacing: .5px;
  }
</style>
</head>
<body>
  <section class="card card--details">
    <div class="brand"><span class="brand__mark"></span><span class="brand__name">Restwell</span></div>
    <div class="divider"></div>
    <div class="contact">
      <p class="contact__name">DANIEL MERCER</p>
      <p class="contact__title">Managing Director</p>
      <p class="contact__row">
        <svg viewBox="0 0 16 16"><path fill="#7d9dcb" d="M3 1l3 3-1.5 2a9 9 0 0 0 5.5 5.5L12 10l3 3-2 2C7 15 1 9 1 3z"/></svg>
        044-555 0142 78
      </p>
      <p class="contact__row">
        <svg viewBox="0 0 16 16"><rect x="1" y="3" width="14" height="10" fill="#7d9dcb"/><path d="M1 3l7 6 7-6" stroke="#0e0e0e" stroke-width="1.4" fill="none"/></svg>
        info@restwellvet.com
      </p>
      <p class="contact__row">
        <svg viewBox="0 0 16 16"><circle cx="8" cy="8" r="6.5" stroke="#7d9dcb" stroke-width="1.4" fill="none"/><path d="M1.5 8h13M8 1.5c-3 3.5-3 9.5 0 13M8 1.5c3 3.5 3 9.5 0 13" stroke="#7d9dcb" stroke-width="1.1" fill="none"/></svg>
        <span>www.<span class="accent">restwellvet</span>.com</span>
      </p>
      <p class="contact__address">421, Address line goes here<br>45452,Country Name</p>
    </div>
    <div class="tagline-band">PEACEFUL AND COMPASSIONATE AT-HOME PET EUTHANASIA</div>
  </section>

  <section class="card card--photo">
    <div class="photo-fill" role="img" aria-label="Black and white photo of a person cuddling a tabby cat"></div>
    <div class="brand"><span class="brand__mark"></span><span class="brand__name">Restwell</span></div>
    <p class="brand-line">A GIFT OF LOVE AT HOME</p>
  </section>
</body>
</html>
```